Coral Bay Pools New website

I currently operate a swimming pool service and repair business and looking for a re design for my website as it has been over 5 years since it was designed. current site is coralbaypoolslv.com

```html
<!DOCTYPE html>
<html lang="en">
<head>
<meta charset="utf-8">
<title>Coral Bay Pools – Local Pool Cleaning</title>
<link href="https://fonts.googleapis.com/css2?family=Outfit:wght@600;700;800&family=DM+Sans:wght@400;500;700&family=Yellowtail&display=swap" rel="stylesheet">
<style>
:root{
  --blue:#0b98e8;
  --blue-deep:#0d5fa5;
  --navy:#0a4f8c;
  --orange:#f6a01a;
  --ink:#111418;
  --text:#2a2f36;
  --mist:#e7eff3;
  --white:#ffffff;
}
*{box-sizing:border-box;margin:0;padding:0}
html,body{width:1200px;height:3828px;overflow:hidden;background:var(--white)}
body{position:relative;font-family:"DM Sans",sans-serif;color:var(--text)}
.abs{position:absolute}
h1,h2,h3{font-family:"Outfit",sans-serif;font-weight:800;color:var(--ink);letter-spacing:-.5px}
.accent{color:var(--blue-deep)}
.btn{position:absolute;display:flex;align-items:center;justify-content:center;background:var(--blue);color:var(--white);font-family:"DM Sans",sans-serif;font-weight:700;font-size:15px;letter-spacing:.3px;border-radius:3px}
.label{position:absolute;display:flex;gap:3px}
.label span{width:22px;height:22px;border:1.5px solid var(--orange);border-radius:50%;display:flex;align-items:center;justify-content:center;font-family:"Outfit",sans-serif;font-weight:600;font-size:11px;color:var(--blue-deep);background:var(--white)}

/* header */
.header{left:0;top:0;width:1200px;height:68px;background:var(--white);z-index:5}
.brand{position:absolute;left:96px;top:8px;width:166px;height:84px;background:var(--white);border-radius:10px;display:flex;align-items:center;justify-content:center;gap:6px;z-index:6}
.brand .dot{width:14px;height:14px;border-radius:50%;background:var(--orange)}
.brand b{font-family:"Outfit",sans-serif;font-weight:700;font-size:17px;color:var(--blue-deep)}
.nav{position:absolute;left:375px;top:26px;display:flex;gap:37px;font-size:13px;font-weight:500;color:var(--blue-deep)}
.nav .active{color:var(--blue)}
.phone-box{position:absolute;left:952px;top:0;width:248px;height:68px;background:var(--blue);color:var(--white)}
.phone-box small{position:absolute;left:36px;top:16px;font-size:10px;font-weight:700}
.phone-box strong{position:absolute;left:36px;top:30px;font-size:18px;font-weight:500}
.phone-diamond{position:absolute;left:-24px;top:14px;width:40px;height:40px}

/* hero */
.hero-photo{left:0;top:0;width:1200px;height:700px;background:linear-gradient(180deg,#6f6a5c 0%,#2f7fae 100%)}
.hero-shade{left:0;top:0;width:1200px;height:700px;background:rgba(10,30,50,.2)}
.hero-script{left:0;top:270px;width:1200px;text-align:center;font-family:"Yellowtail",cursive;font-size:40px;color:var(--orange)}
.hero-title{left:0;top:318px;width:1200px;text-align:center;color:var(--white);font-size:60px;letter-spacing:-1px}
.hero-sub{left:0;top:396px;width:1200px;text-align:center;color:var(--white);font-size:17px;font-weight:700}

/* about */
.about-bg{left:0;top:600px;width:1200px;height:710px;background:linear-gradient(180deg,#eef3f4 0%,#f5f7f8 100%)}
.about-mark{left:85px;top:850px;width:505px;height:340px;display:flex;align-items:center;justify-content:center;gap:14px}
.about-mark .dot{width:36px;height:36px;border-radius:50%;background:var(--orange)}
.about-mark b{font-family:"Outfit",sans-serif;font-weight:700;font-size:40px;color:var(--blue-deep)}
.about-title{left:626px;top:872px;font-size:43px;line-height:50px}
.about-text{left:626px;top:986px;width:490px;font-size:15px;line-height:26.5px}

/* services */
.services{left:0;top:1310px;width:1200px;height:910px;background:var(--mist)}
.services-title{left:0;top:1436px;width:1200px;text-align:center;font-size:43px}
.card{position:absolute;top:1535px;width:326px;height:585px;filter:drop-shadow(0 6px 14px rgba(10,60,100,.12))}
.card-shape{position:absolute;inset:0;background:var(--white);clip-path:polygon(50% 0,100% 9%,100% 91%,50% 100%,0 91%,0 9%);border-radius:8px}
.card.featured .card-shape{background:var(--blue-deep)}
.card-photo{position:absolute;left:12px;top:12px;width:302px;height:320px;clip-path:polygon(50% 0,100% 18%,100% 82%,50% 100%,0 82%,0 18%)}
.card h3{position:absolute;left:0;top:364px;width:326px;text-align:center;font-size:23px;font-weight:700}
.card p{position:absolute;left:30px;top:404px;width:266px;text-align:center;font-size:14.5px;line-height:26.5px}
.card.featured h3,.card.featured p{color:var(--white)}
.card-arrow{position:absolute;left:136px;top:510px;width:54px;height:60px}

/* why */
.why-title{left:86px;top:2346px;font-size:43px}
.why-text{left:86px;top:2413px;width:410px;font-size:15px;line-height:26.5px}
.why-text p+p{margin-top:26px}
.why-photo{left:575px;top:2315px;width:540px;height:378px}

/* contact */
.contact-band{left:0;top:2740px;width:1200px;height:653px}
.form-box{left:86px;top:2920px;width:532px;height:362px;border:1.5px solid var(--orange);border-radius:4px;background:rgba(8,60,110,.35)}
.field{position:absolute;background:var(--white);border-radius:2px;display:flex;align-items:flex-start;padding-top:15px;padding-left:16px;gap:9px;font-size:14.5px;color:#33414f}
.field svg{flex:none;margin-top:1px}
.send{position:absolute;left:32px;top:272px;width:470px;height:50px;background:var(--blue);color:var(--white);display:flex;align-items:center;justify-content:center;font-weight:700;font-size:15px;border-radius:2px}
.contact-title{left:681px;top:3022px;font-size:43px;color:var(--white);letter-spacing:.5px}
.contact-text{left:681px;top:3090px;width:440px;font-size:14.5px;line-height:26.5px;color:var(--white)}

/* footer */
.footer-rule{position:absolute;left:86px;width:1028px;height:1px;background:#dde3e8}
.footer-brand{left:516px;top:3466px;width:168px;height:104px;background:var(--white);display:flex;align-items:center;justify-content:center;gap:6px}
.footer-brand .dot{width:14px;height:14px;border-radius:50%;background:var(--orange)}
.footer-brand b{font-family:"Outfit",sans-serif;font-weight:700;font-size:18px;color:var(--blue-deep)}
.footer-nav{left:0;top:3586px;width:1200px;display:flex;justify-content:center;gap:50px;font-size:15px;font-weight:500;color:var(--ink)}
.footer-nav span::before{content:"";display:inline-block;width:5px;height:5px;border-radius:50%;background:var(--blue);margin-right:5px;vertical-align:middle}
.info{position:absolute;top:3660px;display:flex;gap:14px;align-items:center}
.info .icon{width:50px;height:50px;border-radius:50%;background:var(--blue-deep);display:flex;align-items:center;justify-content:center}
.info small{display:block;font-size:12px;font-weight:700;color:var(--ink)}
.info span{display:block;font-size:15px;line-height:20px;color:var(--ink)}
.info .big{font-size:18px}
.copyright{left:86px;top:3774px;font-size:14.5px;color:#444}
.social{left:980px;top:3764px;display:flex;gap:12px}
.social span{width:38px;height:38px;border-radius:50%;border:1.5px solid var(--orange);background:var(--white)}
.social span.on{background:var(--orange)}
</style>
</head>
<body>

<header class="abs header">
  <nav class="nav">
    <span class="active">HOME</span><span>ABOUT US</span><span>OUR SERVICES</span><span>FREE ESTIMATE</span><span>CONTACT</span>
  </nav>
  <div class="phone-box">
    <svg class="phone-diamond" viewBox="0 0 40 40"><rect x="8" y="8" width="24" height="24" rx="3" transform="rotate(45 20 20)" fill="#f6a01a"/><path d="M15 14c1 4 4 8 10 11l2-3-3-2-1 1c-2-1-3-3-4-4l1-1-2-3z" fill="#fff"/></svg>
    <small>PHONE:</small>
    <strong>(702) 555-0148</strong>
  </div>
</header>
<div class="brand"><span class="dot"></span><b>Coral Bay Pools</b></div>

<div class="abs hero-photo" role="img" aria-label="Resort pool at dusk with lounge chairs, umbrellas and palm trees"></div>
<div class="abs hero-shade"></div>
<div class="abs hero-script">Nevada's Top Rated</div>
<h1 class="abs hero-title">LOCAL® POOL CLEANING</h1>
<p class="abs hero-sub">We are a full service pool company servicing the Las Vegas Valley.</p>
<div class="btn" style="left:487px;top:442px;width:214px;height:48px">FREE ESTIMATE NOW</div>

<div class="abs about-bg"></div>
<svg class="abs" style="left:0;top:600px" width="1200" height="110" viewBox="0 0 1200 110">
  <polygon points="0,12 600,100 1200,12 1200,110 0,110" fill="#eef3f4"/>
  <polyline points="0,12 600,100" stroke="#f6a01a" stroke-width="7" fill="none"/>
  <polyline points="600,100 1200,12" stroke="#0b98e8" stroke-width="7" fill="none"/>
</svg>
<svg class="abs" style="left:538px;top:660px" width="124" height="72" viewBox="0 0 124 72">
  <polygon points="62,2 120,36 62,70 4,36" fill="#fff" stroke="#e4e9ed" stroke-linejoin="round"/>
  <rect x="54" y="14" width="16" height="24" rx="8" fill="#f6a01a"/>
  <path d="M62 19v12M57 27l5 5 5-5" stroke="#fff" stroke-width="2" fill="none"/>
  <text x="62" y="59" text-anchor="middle" font-family="DM Sans,sans-serif" font-size="9" font-weight="700" fill="#0d5fa5">SCROLL</text>
</svg>

<div class="abs about-mark"><span class="dot"></span><b>Coral Bay Pools</b></div>

<div class="label" style="left:626px;top:839px"><span>A</span><span>B</span><span>O</span><span>U</span><span>T</span><span>U</span><span>S</span></div>
<h2 class="abs about-title">WE ARE A FULL SERVICE<br><span class="accent">POOL COMPANY</span></h2>
<p class="abs about-text">When you need professional pool cleaning services in Nevada, you can count on the professionals at Coral Bay Pools to provide you with superior and prompt solutions. Whether you need assistance with a residential or commercial pool, we’ll vacuum, brush, and thoroughly clean your pool so it’s swim-ready. We’ll also clean your pool filters and inform you of any issues that arise.</p>
<div class="btn" style="left:626px;top:1170px;width:157px;height:50px">LEARN MORE</div>

<section class="abs services"></section>
<div class="label" style="left:493px;top:1404px"><span>S</span><span>E</span><span>R</span><span>V</span><span>I</span><span>C</span><span>E</span><span>S</span></div>
<h2 class="abs services-title">OUR TOP <span class="accent">POOL SERVICES</span></h2>

<div class="card" style="left:86px">
  <div class="card-shape"></div>
  <div class="card-photo" role="img" aria-label="Pool vacuum head and hose cleaning a pool" style="background:linear-gradient(180deg,#5f9cbf,#3a7ea8)"></div>
  <h3>POOL SERVICES</h3>
  <p>When you invested in your pool, you knew it was a long-term investment in both money and time.</p>
  <svg class="card-arrow" viewBox="0 0 54 60"><polygon points="27,1 53,15 53,45 27,59 1,45 1,15" fill="#0b98e8"/><path d="M16 30h21M29 22l8 8-8 8" stroke="#fff" stroke-width="2.4" fill="none"/></svg>
</div>
<div class="card featured" style="left:437px">
  <div class="card-shape"></div>
  <div class="card-photo" role="img" aria-label="Commercial pool beside a modern building with tropical plants" style="background:linear-gradient(180deg,#5a7d8a,#2d6fb8)"></div>
  <h3>COMMERCIAL POOL</h3>
  <p>As a commercial property owner or manager, doing your job well requires you to be mindful.</p>
  <svg class="card-arrow" viewBox="0 0 54 60"><polygon points="27,1 53,15 53,45 27,59 1,45 1,15" fill="#f6a01a"/><path d="M16 30h21M29 22l8 8-8 8" stroke="#fff" stroke-width="2.4" fill="none"/></svg>
</div>
<div class="card" style="left:788px">
  <div class="card-shape"></div>
  <div class="card-photo" role="img" aria-label="Aerial view of a curved residential pool surrounded by trees" style="background:linear-gradient(180deg,#3f7a4a,#2a8cc4)"></div>
  <h3>RESIDENTIAL POOL</h3>
  <p>Here in Southern Nevada, you know it can get really, really hot. That’s why you invested in your pool.</p>
  <svg class="card-arrow" viewBox="0 0 54 60"><polygon points="27,1 53,15 53,45 27,59 1,45 1,15" fill="#0b98e8"/><path d="M16 30h21M29 22l8 8-8 8" stroke="#fff" stroke-width="2.4" fill="none"/></svg>
</div>

<div class="label" style="left:86px;top:2314px"><span>W</span><span>H</span><span>Y</span><span>U</span><span>S</span></div>
<h2 class="abs why-title">WHY <span class="accent">CHOOSE US?</span></h2>
<div class="abs why-text">
  <p>Our full-service pool company proudly serves the entire Las Vegas valley, and we’re certified by the Desert Valley Health Board to maintain the highest level of pool safety.</p>
  <p>If you need repairs, maintenance, scheduled cleanings, or any other pool services, contact us online or by phone today.</p>
</div>
<div class="btn" style="left:86px;top:2648px;width:157px;height:50px">CONTACT US</div>
<svg class="abs why-photo" viewBox="0 0 540 378" role="img" aria-label="Technician lowering a robotic pool cleaner into a pool">
  <polygon points="270,6 534,189 270,372 6,189" fill="#f6a01a" stroke="#f6a01a" stroke-width="20" stroke-linejoin="round"/>
  <polygon points="270,18 516,189 270,360 24,189" fill="#3aa6de" stroke="#0d5fa5" stroke-width="14" stroke-linejoin="round"/>
</svg>

<svg class="abs contact-band" viewBox="0 0 1200 653" role="img" aria-label="Deep blue backdrop of a pool and palm trees">
  <polygon points="0,111 600,4 1200,89 1200,653 0,653" fill="#0d5fa5"/>
  <polyline points="0,111 600,4" stroke="#f6a01a" stroke-width="7" fill="none"/>
  <polyline points="600,4 1200,89" stroke="#0b98e8" stroke-width="7" fill="none"/>
</svg>
<div class="abs form-box">
  <div class="field" style="left:32px;top:40px;width:229px;height:50px"><svg width="13" height="14" viewBox="0 0 13 14"><circle cx="6.5" cy="4" r="3.5" fill="#0d5fa5"/><path d="M0 14c0-4 3-6 6.5-6S13 10 13 14z" fill="#0d5fa5"/></svg>First Name</div>
  <div class="field" style="left:273px;top:40px;width:229px;height:50px"><svg width="13" height="14" viewBox="0 0 13 14"><circle cx="6.5" cy="4" r="3.5" fill="#0d5fa5"/><path d="M0 14c0-4 3-6 6.5-6S13 10 13 14z" fill="#0d5fa5"/></svg>Last Name</div>
  <div class="field" style="left:32px;top:103px;width:229px;height:50px"><svg width="14" height="14" viewBox="0 0 14 14"><path d="M2 1l3 0 1 4-2 1c1 2 2 3 4 4l1-2 4 1 0 3c-7 0-11-4-11-11z" fill="#0d5fa5"/></svg>Phone Number</div>
  <div class="field" style="left:273px;top:103px;width:229px;height:50px"><svg width="15" height="12" viewBox="0 0 15 12"><rect width="15" height="12" rx="1.5" fill="#0d5fa5"/><path d="M1 2l6.5 5L14 2" stroke="#fff" fill="none"/></svg>Email Address</div>
  <div class="field" style="left:32px;top:167px;width:470px;height:93px"><svg width="15" height="14" viewBox="0 0 15 14"><path d="M1 1h13v9H5l-3 3v-3H1z" fill="#0d5fa5"/></svg>Type your message...</div>
  <div class="send">SEND MESSAGE</div>
</div>
<div class="label" style="left:681px;top:2990px"><span>C</span><span>O</span><span>N</span><span>T</span><span>A</span><span>C</span><span>T</span><span>U</span><span>S</span></div>
<h2 class="abs contact-title">CONTACT &nbsp;WITH US</h2>
<p class="abs contact-text">At Coral Bay Pools, we understand that homeowners don’t always have time to take care of their pools. You have a long list of other responsibilities to tend to, so why not hire a professional pool cleaning service to handle your pool maintenance and upkeep for you?</p>

<div class="footer-rule" style="top:3520px"></div>
<div class="abs footer-brand"><span class="dot"></span><b>Coral Bay Pools</b></div>
<nav class="abs footer-nav"><span>Home</span><span>About Us</span><span>Our Services</span><span>Free Estimate</span><span>Contact</span></nav>
<div class="footer-rule" style="top:3632px"></div>

<div class="info" style="left:119px">
  <div class="icon"><svg width="16" height="20" viewBox="0 0 16 20"><path d="M8 0a8 8 0 0 1 8 8c0 6-8 12-8 12S0 14 0 8a8 8 0 0 1 8-8z" fill="#fff"/><circle cx="8" cy="8" r="3" fill="#0d5fa5"/></svg></div>
  <div><small>ADDRESS</small><span>Sed ut perspiciatis unde<br>omnis iste natus</span></div>
</div>
<div class="info" style="left:449px">
  <div class="icon"><svg width="18" height="14" viewBox="0 0 18 14"><rect width="18" height="14" rx="2" fill="#fff"/><path d="M1 2l8 6 8-6" stroke="#0d5fa5" stroke-width="1.5" fill="none"/></svg></div>
  <div><small>EMAIL US</small><span>poolsolutions@coralbaypoolslv.com</span></div>
</div>
<div class="info" style="left:891px">
  <div class="icon"><svg width="18" height="18" viewBox="0 0 14 14"><path d="M2 1l3 0 1 4-2 1c1 2 2 3 4 4l1-2 4 1 0 3c-7 0-11-4-11-11z" fill="#fff"/></svg></div>
  <div><small>CALL US</small><span class="big">(702) 555-0148</span></div>
</div>
<div class="footer-rule" style="top:3745px"></div>

<p class="abs copyright">©2026 Coral Bay Pools. - All rights reserved.</p>
<div class="abs social"><span></span><span class="on"></span><span></span></div>

</body>
</html>
```